Consulting company requires a logo and business card design

I require a logo/business card design for a new company based in Sexsmith Alberta called TallMarsh Integrity Consulting Ltd. I plan to provide the following services: Construction management/inspection for the oil and gas industry, as well as general consulting for Asset Management, fleet management, etc. Have attached a copy of resume for use as guide for

Target Market(s)

Businesses within the oil and gas production, construction and shipping industry

Industry/Entity Type

Oil And Gas

Contact Information for Business Card

Believe should highlight, services offered, safety, quality,

Logo Text

TallMarsh Integrity Consulting (TMIC) ?

Font styles to use
Script

Requirements
Must have
• Open to all options

```html
<!DOCTYPE html>
<html lang="en">
<head>
<meta charset="utf-8">
<title>TallMarsh Integrity Consulting Ltd – Business Card</title>
<link rel="stylesheet" href="https://fonts.googleapis.com/css2?family=Lato:wght@400;700&display=swap">
<style>
  :root {
    --crimson: #c81a3e;
    --card-light: #f3f3f3;
    --ink: #3a3a3a;
    --rule: #c9c9c9;
    --rule-on-red: rgba(255,255,255,0.45);
    --stage-top: #2b2b2b;
    --stage-bottom: #060606;
    --white: #ffffff;
  }
  * { box-sizing: border-box; margin: 0; padding: 0; }
  html, body {
    width: 1200px; height: 900px; overflow: hidden;
  }
  body {
    background: linear-gradient(to bottom, var(--stage-top), var(--stage-bottom));
    font-family: "Lato", Arial, sans-serif;
    position: relative;
  }
  .card {
    position: absolute;
    top: 184px;
    height: 490px;
    border-radius: 12px;
    text-align: center;
  }
  .card--front {
    left: 299px; width: 301px;
    background: var(--card-light);
  }
  .card--back {
    left: 645px; width: 305px;
    background: var(--crimson);
  }
  .brand-dot {
    position: absolute;
    left: 50%; top: 48px;
    width: 62px; height: 62px;
    margin-left: -31px;
    border-radius: 50%;
    background: var(--crimson);
  }
  .brand-name {
    position: absolute; left: 0; right: 0;
    font-weight: 700;
    font-size: 25px;
    letter-spacing: -0.2px;
    line-height: 1;
  }
  .brand-sub {
    position: absolute; left: 22px; right: 22px;
    display: flex; align-items: center; gap: 8px;
    font-size: 15px;
    letter-spacing: 4.2px;
    line-height: 1;
  }
  .brand-sub::before, .brand-sub::after {
    content: ""; flex: 1; height: 1px;
  }
  .card--front .brand-name { top: 143px; color: var(--crimson); }
  .card--front .brand-sub { top: 174px; color: var(--ink); }
  .card--front .brand-sub::before,
  .card--front .brand-sub::after { background: var(--rule); }
  .card--back .brand-name { top: 399px; color: var(--white); }
  .card--back .brand-sub { top: 428px; color: var(--white); left: 28px; right: 28px; }
  .card--back .brand-sub::before,
  .card--back .brand-sub::after { background: var(--rule-on-red); }

  .person { position: absolute; top: 268px; left: 0; right: 0; }
  .person__name {
    color: var(--crimson); font-weight: 700; font-size: 19px; line-height: 1.2;
  }
  .person__role { color: var(--ink); font-size: 14.5px; margin-top: 3px; }

  .contact {
    position: absolute; top: 342px; left: 0; right: 0;
    list-style: none; color: var(--ink); font-size: 14.5px; line-height: 20px;
  }
  .contact li { display: flex; justify-content: center; align-items: center; gap: 9px; }
  .contact svg { width: 10px; height: 10px; fill: var(--crimson); }

  .address {
    position: absolute; top: 419px; left: 0; right: 0;
    font-style: normal; color: var(--ink); font-size: 14px; line-height: 17px;
  }
</style>
</head>
<body>
  <section class="card card--front" aria-label="Business card front">
    <span class="brand-dot" aria-hidden="true"></span>
    <p class="brand-name">TallMarsh Integrity</p>
    <p class="brand-sub">Consulting Ltd</p>

    <div class="person">
      <p class="person__name">DANA WHITLOCK</p>
      <p class="person__role">Managing Director</p>
    </div>

    <ul class="contact">
      <li>
        <svg viewBox="0 0 10 10" aria-hidden="true"><path d="M0 4 Q5 0 10 4 L10 5 L7.5 5 L7 3.8 L3 3.8 L2.5 5 L0 5 Z M2 6 L8 6 L9 9.5 L1 9.5 Z"/></svg>
        <span>587-555-0142</span>
      </li>
      <li>
        <svg viewBox="0 0 10 10" aria-hidden="true"><path d="M0 2 L10 2 L10 3 L5 6 L0 3 Z M0 4.2 L5 7.2 L10 4.2 L10 8.5 L0 8.5 Z"/></svg>
        <span>hello@tallmarsh.example</span>
      </li>
    </ul>

    <address class="address">48 Birch Lane<br>Sexsmith, AB T0H 3C0</address>
  </section>

  <section class="card card--back" aria-label="Business card back">
    <p class="brand-name">TallMarsh Integrity</p>
    <p class="brand-sub">Consulting Ltd</p>
  </section>
</body>
</html>
```